Executive Business Card for Healthcare Company [Need Today]

I need a business card design for a healthcare company. The only branding the company has thus far is a logo. The cards will be utilized by company executives. The design I envision will be vibrant and appealing but with a corporate feel. They shouldn't be too casual or playful. I would like to complete this project TODAY if possible.

Target Market(s)

Healthcare vendors, other executives in healthcare and pharmaceuticals

Industry/Entity Type

Pharmaceutical

Contact Information for Business Card

See attachment

Font styles to use
Serif
Sans Serif

Colors

Designer to choose colors to be used in the design.

```html
<!DOCTYPE html>
<html lang="en">
<head>
<meta charset="utf-8">
<title>Tallis Therapeutics — Executive Business Card</title>
<link rel="stylesheet" href="https://fonts.googleapis.com/css2?family=Open+Sans:wght@400;600&family=Rubik:wght@400&display=swap">
<style>
  :root {
    --teal: #3bbfc6;
    --mint: #5fc293;
    --ink: #555a5e;
    --rule: #b9bcbf;
    --card: #ffffff;
    --backdrop: #d9d9d7;
  }
  * { margin: 0; padding: 0; box-sizing: border-box; }
  html, body { width: 1200px; height: 1000px; overflow: hidden; }
  body {
    position: relative;
    background: var(--backdrop);
    font-family: "Open Sans", Arial, sans-serif;
  }
  .card {
    position: absolute;
    background: var(--card);
    border-radius: 36px;
    box-shadow: 0 6px 14px rgba(0,0,0,0.18);
  }
  .card--front { left: 148px; top: 98px; width: 634px; height: 362px; }
  .card--back  { left: 372px; top: 546px; width: 636px; height: 362px; }

  .front-frame {
    position: absolute;
    left: 26px; top: 27px; right: 26px; bottom: 28px;
    border: 2px solid var(--teal);
    border-radius: 28px;
  }
  .front-wordmark {
    position: absolute;
    left: 70px; top: 120px;
    font-size: 62px; font-weight: 400;
    color: var(--teal);
    letter-spacing: 1px;
  }

  .lockup {
    position: absolute;
    display: flex; align-items: center; gap: 10px;
  }
  .lockup__circle {
    width: 74px; height: 74px;
    border: 3px solid var(--mint);
    border-radius: 50%;
  }
  .lockup__name {
    font-size: 22px; font-weight: 400;
    color: var(--teal);
    line-height: 1.05;
  }
  .card--front .lockup { left: 358px; top: 143px; }
  .card--back .lockup  { left: 366px; top: 62px; }

  .person { position: absolute; left: 42px; top: 72px; }
  .person__name {
    font-family: "Rubik", Arial, sans-serif;
    font-size: 31px; letter-spacing: 2px;
    color: var(--teal);
  }
  .person__title {
    margin-top: 2px;
    font-size: 18px; color: var(--ink);
  }
  .divider {
    position: absolute; left: 40px; right: 38px; top: 177px;
    border-top: 1.5px solid var(--rule);
  }
  .contacts { position: absolute; left: 40px; top: 196px; list-style: none; }
  .contacts li {
    display: flex; align-items: center; gap: 16px;
    height: 29px;
    font-size: 21px; letter-spacing: 1px; color: var(--ink);
  }
  .contacts svg { width: 20px; height: 20px; fill: var(--ink); }
  .company {
    position: absolute; left: 0; right: 0; top: 305px;
    text-align: center;
    font-size: 15px; line-height: 1.3;
    color: var(--teal);
  }
</style>
</head>
<body>

<section class="card card--front">
  <div class="front-frame"></div>
  <div class="front-wordmark">tallis</div>
  <div class="lockup">
    <span class="lockup__circle"></span>
    <span class="lockup__name">tallis<br>therapeutics</span>
  </div>
</section>

<section class="card card--back">
  <div class="person">
    <h1 class="person__name">Daniel Reeve</h1>
    <p class="person__title">Senior Director of Marketing</p>
  </div>
  <div class="lockup">
    <span class="lockup__circle"></span>
    <span class="lockup__name">tallis<br>therapeutics</span>
  </div>
  <div class="divider"></div>
  <ul class="contacts">
    <li>
      <svg viewBox="0 0 20 20" aria-hidden="true"><path d="M2 6c0-2 3-3 8-3s8 1 8 3v2h-4V6.5c-1-.4-2.5-.6-4-.6s-3 .2-4 .6V8H2zM5 9h10l2 8H3zm5 2a2.5 2.5 0 100 5 2.5 2.5 0 000-5z"/></svg>
      <span>555-214-0187</span>
    </li>
    <li>
      <svg viewBox="0 0 20 20" aria-hidden="true"><path d="M4 2l3 0 2 4-2 2c1 2 3 4 5 5l2-2 4 2v3c0 1-1 2-2 2C9 18 2 11 2 4c0-1 1-2 2-2z"/></svg>
      <span>555-302-4461</span>
    </li>
    <li>
      <svg viewBox="0 0 20 20" aria-hidden="true"><path d="M2 5h16v10H2zm1.5 1.2L10 11l6.5-4.8V6H3.5z"/></svg>
      <span>dreeve@tallisrx.com</span>
    </li>
  </ul>
  <p class="company">TALLIS THERAPEUTICS, LLC<br>118 W Harbor Street, Milford, GA 30999</p>
</section>

</body>
</html>
```